Pebble Hop - mobile play centre poster designs

Who are we - we are a mobile playground business that specialises in providing entertainment to children in a safe, clean environment either at home or in a function centre. Brief - create 4 different signs to be displayed on our playgrounds. Please find attached 3 photos from our competitors to use as a guide. Corflute sign - size A1 Toddler zone - size A1 Playground rules - size A4 No climbing - size 20cmx8cm sending through photos and documents now.
Colors
Designer to choose colors to be used in the design.
Requirements
Must have
- Colour, be very specific with the rules, pictures

```html
<!DOCTYPE html>
<html lang="en">
<head>
<meta charset="UTF-8">
<title>No Climbing Sign</title>
<link rel="stylesheet" href="https://fonts.googleapis.com/css2?family=Anton&display=swap">
<style>
  :root {
    --frame-green: #00a651;
    --sign-white: #ffffff;
    --warning-red: #ed1c24;
    --mesh-tint: #d6efe0;
    --mesh-tint-deep: #b9e3c9;
  }
  html, body {
    margin: 0;
    padding: 0;
    overflow: hidden;
    background: var(--sign-white);
  }
  .sign {
    position: relative;
    width: 1200px;
    height: 480px;
    box-sizing: border-box;
    background: var(--frame-green);
    padding: 42px;
  }
  .sign-panel {
    position: relative;
    width: 100%;
    height: 100%;
    background: var(--sign-white);
  }
  .climber-pictogram {
    position: absolute;
    left: 35px;
    top: 53px;
    width: 275px;
    height: 275px;
    background: linear-gradient(135deg, var(--mesh-tint), var(--mesh-tint-deep));
  }
  .sign-heading {
    position: absolute;
    left: 344px;
    top: 0;
    width: 760px;
    height: 396px;
  }
  .sign-heading text {
    font-family: "Anton", "Impact", sans-serif;
    fill: var(--warning-red);
  }
</style>
</head>
<body>
  <div class="sign">
    <div class="sign-panel">
      <div class="climber-pictogram" role="img" aria-label="Red pictogram of a person climbing a green chain-link fence"></div>
      <svg class="sign-heading" viewBox="0 0 760 396" aria-label="No climbing">
        <text x="0" y="301" font-size="298" textLength="746" lengthAdjust="spacingAndGlyphs">NO CLIMBING</text>
      </svg>
    </div>
  </div>
</body>
</html>
```